Baby Adoption Announcement

I'm looking for a simple, understated and modern baby adoption announcement.

The baby is a boy, but I don't want anything that is blue or particularly boyish. No storks, baby baskets, rattles, or traditional baby announcement designs. No cutesy or busy designs.

Should measure 5.25 x 8.25 inches to fit in an A9 envelope.

Simple graphics MIGHT include birds, grasses, trees, rivers. I'm open to other ideas. Text can be a single color or multi colored. Graphics are not mandatory.

Since this is text heavy, I'd like the designer to be REALLY GOOD at choosing fonts and typesetting.

Text should read:

Memory answers us bright on your face—
Impossibly, we spoke and were silent
Together before all of this. (in italics)

Tobias Aldric Pelt Ostry
Born on March 16, 2012 in Boston, MA
and entrusted to us by his birthmother, Greta.

Named Tobias, which means God is with us, after Greta’s grandfather &
Aldric, after Al and St. Aldric of Myra

Requirements
Must have
• Should measure 5.25 x 8.25 inches to fit in A9 envelope.

Should not have
• The baby is a boy, but I don't want anything that is blue or particularly boyish. No storks, baby baskets, rattles, or traditional baby announcement designs. Nothing cutesy or busy.

```html
<!DOCTYPE html>
<html lang="en">
<head>
<meta charset="utf-8">
<title>Adoption Announcement – Tobias Aldric Pelt Ostry</title>
<link rel="stylesheet" href="https://fonts.googleapis.com/css2?family=Petit+Formal+Script&family=Cinzel:wght@500&family=Gentium+Book+Plus&display=swap">
<style>
  :root {
    --paper: #ffffff;
    --panel-line: #cfcfcf;
    --stamp-grey: #d4d4d4;
    --frame-green: #5a6b34;
    --frame-brown: #98672a;
    --frame-sage: #a3ad6c;
    --ink-gold: #8a6a22;
    --ink-brown: #6e4f14;
    --ink-green: #4f6a2c;
  }
  * { margin: 0; padding: 0; box-sizing: border-box; }
  html, body {
    width: 1200px; height: 802px; overflow: hidden;
    background: var(--paper);
  }
  .sheet { position: relative; width: 1200px; height: 802px; }

  .address-panel {
    position: absolute; left: 0; top: 0;
    width: 302px; height: 802px;
    border: 2px solid var(--panel-line);
  }
  .stamp-label {
    position: absolute; left: 151px; top: 412px;
    transform: translate(-50%, -50%) rotate(90deg);
    font-family: "Gentium Book Plus", serif;
    font-size: 22px; letter-spacing: 2px;
    color: var(--stamp-grey);
  }

  .frame { position: absolute; left: 342px; top: 21px; }

  .message {
    position: absolute; left: 380px; top: 0; width: 744px; height: 802px;
    text-align: center;
  }
  .message > * { position: absolute; left: 0; width: 100%; white-space: nowrap; }

  .headline {
    top: 102px;
    font-family: "Petit Formal Script", cursive;
    font-weight: 400; font-size: 37px; line-height: 50px;
    color: var(--ink-gold);
  }
  .verse {
    top: 201px;
    font-family: "Petit Formal Script", cursive;
    font-size: 26px; line-height: 46.5px;
    color: var(--ink-gold);
  }
  .child-name {
    top: 370px;
    font-family: "Cinzel", serif; font-weight: 500;
    font-size: 40px; line-height: 50px; letter-spacing: 2.5px;
    color: var(--ink-brown);
  }
  .birth, .naming {
    font-family: "Gentium Book Plus", serif;
    font-size: 25px;
    color: var(--ink-gold);
  }
  .birth { top: 448px; line-height: 40px; }
  .naming { top: 564px; line-height: 42px; }
  .birthmother {
    font-family: "Petit Formal Script", cursive;
    font-size: 27px; color: var(--ink-green);
  }
  .meaning {
    font-family: "Cinzel", serif; font-size: 25px;
    color: var(--ink-green);
  }
  .small-caps {
    font-family: "Cinzel", serif; font-size: 25px;
    color: var(--ink-brown);
  }
</style>
</head>
<body>
<main class="sheet">
  <aside class="address-panel">
    <span class="stamp-label">STAMP</span>
  </aside>

  <svg class="frame" width="820" height="762" viewBox="0 0 820 762" aria-hidden="true">
    <rect x="3.5" y="3.5" width="813" height="755" rx="24" fill="none" stroke="var(--frame-green)" stroke-width="7"/>
    <rect x="16.5" y="16.5" width="787" height="729" rx="18" fill="none" stroke="var(--frame-brown)" stroke-width="7"/>
    <rect x="29.5" y="29.5" width="761" height="703" rx="14" fill="var(--paper)" stroke="var(--frame-sage)" stroke-width="7"/>
  </svg>

  <section class="message">
    <h1 class="headline">We Welcome with Joy</h1>
    <p class="verse">
      Memory answers us bright on your face<br>
      Impossibly, we spoke and were silent<br>
      Together before all of this
    </p>
    <h2 class="child-name">Tobias Aldric Pelt Ostry</h2>
    <p class="birth">
      Born on March 16, 2012 in Boston, MA<br>
      and entrusted to us by his birthmother, <span class="birthmother">Greta</span>.
    </p>
    <p class="naming">
      Named Tobias, which means <span class="meaning">God is with us</span><br>
      after Greta’s grandfather &amp;<br>
      <span class="small-caps">Aldric</span>, after Al and <span class="small-caps">St. Aldric of Myra</span>
    </p>
  </section>
</main>
</body>
</html>
```